Business card design needed

I run a Beautician studio (for 7 years now)
I offer
- Velmo Body Sugaring
- Ruby Glaze
- Nails
- Facials
- Manicure
- Foot Treatment
It might not be necessary to list all those treatments?
Maybe the link to the Website is sufficient?
I leave that up to you ...
(more info on www.FernAndDewByLenka.com.au)
Velmo BodySugaring is our biggest success, It replaces waxing.
I would like to incorporate the logo into the Business Card.
We had many complaints regarding our old Business Cards as the Phone Number was to small.
On the backside, we would like a "your next Appointment" section.
Looking forward to you Design, cheers ... Lenka
Industry/Entity Type
Business
Contact Information for Business Card
Fern by Dew by Lenka
14 Korrin Sqr 3942 Calder
www.FernAndDewByLenka.com.au
03 9481 2267

```html
<!DOCTYPE html>
<html lang="en">
<head>
<meta charset="utf-8">
<title>Fern &amp; Dew by Lenka – Business Card</title>
<link rel="stylesheet" href="https://fonts.googleapis.com/css2?family=Tenor+Sans&family=Open+Sans:ital,wght@0,400;0,600;1,600;1,700&family=Tinos&display=swap">
<style>
  :root {
    --stage: #e9e7e4;
    --card: #ffffff;
    --ink: #2f2f31;
    --ink-soft: #444446;
    --rule: #8a8a8c;
    --band-dark: #3b3b3d;
    --band-light: #6c6c6e;
    --logo-ink: #3a3a3c;
    --logo-dot: #f0a323;
    --watermark: #ececec;
  }
  * { box-sizing: border-box; margin: 0; padding: 0; }
  html, body { width: 1200px; height: 788px; overflow: hidden; }
  body {
    background: var(--stage);
    position: relative;
    font-family: "Open Sans", Arial, sans-serif;
    color: var(--ink);
  }
  .view-label {
    position: absolute;
    font-size: 21px;
    color: #222;
    transform: translateX(-50%);
  }
  .card {
    position: absolute;
    width: 524px;
    height: 300px;
    background: var(--card);
    border-radius: 22px;
    overflow: hidden;
    box-shadow: 0 6px 14px rgba(0,0,0,.22);
  }
  .card > * { position: absolute; }
  .brand-title {
    font-family: "Tenor Sans", Arial, sans-serif;
    color: var(--ink-soft);
    white-space: nowrap;
  }
  .logo-mark {
    display: flex;
    flex-direction: column;
    align-items: center;
    gap: 6px;
  }
  .logo-mark .dot {
    width: 44px; height: 44px; border-radius: 50%;
    background: var(--logo-dot);
  }
  .logo-mark .name {
    font-family: "Tenor Sans", Arial, sans-serif;
    color: var(--logo-ink);
    font-size: 20px;
    letter-spacing: 3px;
    white-space: nowrap;
  }

  /* Front */
  .card-front { left: 338px; top: 74px; }
  .card-front .brand-title { top: 42px; width: 100%; text-align: center; font-size: 40px; letter-spacing: 1px; }
  .card-front .web { top: 102px; width: 100%; text-align: center; font-size: 16px; }
  .card-front .web em { font-weight: 700; }
  .card-front .logo-mark { left: 48px; top: 182px; width: 130px; }
  .card-front .band { left: 0; top: 246px; width: 524px; height: 54px; }
  .card-front .contact { left: 300px; top: 252px; color: #fff; font-size: 16px; line-height: 22px; }
  .card-front .contact em { font-weight: 700; }

  /* Back 1 */
  .card-back-services { left: 54px; top: 444px; }
  .card-back-services .brand-title { top: 12px; width: 100%; text-align: center; font-size: 25px; letter-spacing: 1px; }
  .card-back-services .head-rule { top: 50px; left: 0; width: 100%; height: 1px; background: var(--rule); }
  .card-back-services .watermark {
    left: 110px; top: 170px;
    font-family: "Tenor Sans", Arial, sans-serif;
    font-size: 50px; letter-spacing: 8px;
    color: var(--watermark);
  }
  .section-head { font-style: italic; font-weight: 700; font-size: 17px; color: var(--ink); }
  .card-back-services .offer-head { left: 29px; top: 69px; }
  .service-list { left: 29px; top: 97px; list-style: none; font-family: "Tinos", "Times New Roman", serif; font-size: 15px; line-height: 20px; color: #333; }
  .service-list li::before { content: "▪"; font-size: 10px; margin-right: 6px; vertical-align: 2px; }
  .card-back-services .divider { left: 207px; top: 70px; width: 2px; height: 144px; background: #777; }
  .card-back-services .appt-head { left: 243px; top: 69px; }
  .fill-row { font-size: 16px; display: flex; align-items: flex-end; white-space: nowrap; }
  .fill-row .blank { display: inline-block; border-bottom: 1px solid var(--ink); height: 18px; }
  .card-back-services .row-name { left: 243px; top: 110px; }
  .card-back-services .row-date { left: 243px; top: 150px; }
  .card-back-services .row-time { left: 243px; top: 190px; }
  .card-back-services .hours-head { top: 238px; width: 100%; text-align: center; font-style: italic; font-weight: 600; font-size: 14px; }
  .card-back-services .hours-line { top: 261px; left: 61px; font-size: 13px; word-spacing: 1px; }
  .card-back-services .hours-line span + span { margin-left: 46px; }

  /* Back 2 */
  .card-back-booking { left: 622px; top: 444px; }
  .card-back-booking .hours-head { left: 32px; top: 26px; font-style: italic; font-weight: 600; font-size: 20px; letter-spacing: 1.5px; }
  .card-back-booking .hours-lines { left: 30px; top: 60px; font-size: 17px; line-height: 24px; }
  .card-back-booking .logo-mark { left: 378px; top: 26px; width: 120px; }
  .card-back-booking .head-rule { left: 28px; top: 116px; width: 468px; height: 1px; background: #bbb; }
  .card-back-booking .row-who { left: 45px; top: 142px; font-size: 18px; }
  .card-back-booking .row-date { left: 34px; top: 192px; font-size: 18px; gap: 0; }
  .card-back-booking .row-date .blank { margin: 0 6px; }
  .day-boxes { left: 59px; top: 248px; display: flex; gap: 14px; font-size: 17px; }
  .day-boxes span { display: flex; align-items: center; gap: 10px; }
  .day-boxes i { width: 23px; height: 23px; border: 1.5px solid var(--ink); display: inline-block; }
</style>
</head>
<body>

<div class="view-label" style="left:600px; top:32px;">Front</div>
<div class="view-label" style="left:324px; top:402px;">Back - 1</div>
<div class="view-label" style="left:896px; top:402px;">Back - 2</div>

<section class="card card-front">
  <h1 class="brand-title">FERN&amp;DEW BY LENKA</h1>
  <p class="web"><em>web</em> www.FernAndDewByLenka.com.au</p>
  <div class="logo-mark"><span class="dot"></span><span class="name">VELMO</span></div>
  <svg class="band" viewBox="0 0 524 54" width="524" height="54">
    <polygon points="0,28 275,28 260,44 0,44" fill="var(--band-light)"/>
    <polygon points="0,47 256,47 249,54 0,54" fill="var(--band-dark)"/>
    <polygon points="290,2 524,2 524,54 258,54" fill="var(--band-dark)"/>
  </svg>
  <p class="contact"><em>phone</em> 03 9481 2267<br>14 Korrin Sqr, 3942 Calder</p>
</section>

<section class="card card-back-services">
  <span class="watermark">VELMO</span>
  <h2 class="brand-title">FERN&amp;DEW BY LENKA</h2>
  <div class="head-rule"></div>
  <h3 class="section-head offer-head">I offer</h3>
  <ul class="service-list">
    <li>Velmo Body Sugaring</li>
    <li>Ruby Glaze</li>
    <li>Nails</li>
    <li>Facials</li>
    <li>Manicure</li>
    <li>Foot Treatment</li>
  </ul>
  <div class="divider"></div>
  <h3 class="section-head appt-head">An Appointment</h3>
  <p class="fill-row row-name">Name<span class="blank" style="width:216px"></span></p>
  <p class="fill-row row-date">Date<span class="blank" style="width:226px"></span></p>
  <p class="fill-row row-time">time<span class="blank" style="width:160px"></span>&nbsp;am / pm</p>
  <h3 class="hours-head">Hours of Operation</h3>
  <p class="hours-line"><span>Mon. to Fri.&nbsp; 7.30am - 7.00pm</span><span>Sat. 7.30am - 12.00pm</span></p>
</section>

<section class="card card-back-booking">
  <h2 class="hours-head">Hours of Operation</h2>
  <p class="hours-lines">Monday to Friday -&nbsp; 7.30am - 7.00pm<br>Saturday - 7.30am - 12.00pm</p>
  <div class="logo-mark"><span class="dot"></span><span class="name">VELMO</span></div>
  <div class="head-rule"></div>
  <p class="fill-row row-who"><span class="blank" style="width:260px"></span>&nbsp;has an appointment</p>
  <p class="fill-row row-date">Date :<span class="blank" style="width:40px"></span>/<span class="blank" style="width:42px"></span>/<span class="blank" style="width:52px"></span>@<span class="blank" style="width:40px"></span>:<span class="blank" style="width:50px"></span>am / pm</p>
  <div class="day-boxes">
    <span><i></i>Mon.</span>
    <span><i></i>Tue.</span>
    <span><i></i>Wed.</span>
    <span><i></i>Thu.</span>
    <span><i></i>Fri.</span>
  </div>
</section>

</body>
</html>
```